Poster for Kirtan Music Event

Design (3) 24" x 36" Posters

I have provided a sample a friend did in Australia: ( Picture No. 4 )

Use all the text on sample poster except the replacement changes below.

Replace with the following text as this is for different location:
Replacement Text:

Every Friday Night 7:00pm-8:30pm
Kealoha Pilates & Movement Studio
947 Hollister Rd Paia

Free Kirtan Experience! or Free Event
Mohan Priya Sevi & Companions

Optional Text:

A evening of music, singing of spiritual mantras, and refreshments

Bring flowers, musical instruments, friends, or just come with an open heart.

Meditate on transcendental sounds that provide rest for the mind & heart"

An evening of music & singing of sacred mantra's

```html
<!DOCTYPE html>
<html lang="en">
<head>
<meta charset="utf-8">
<title>Kirtan Experience Poster</title>
<link rel="stylesheet" href="https://fonts.googleapis.com/css2?family=Tillana:wght@500;700;800&family=Kaushan+Script&family=Tiro+Devanagari+Hindi&display=swap">
<style>
  :root {
    --green-deep: #1f5a1c;
    --green-mid: #3f8a2e;
    --green-light: #5fa83e;
    --orange: #f07a1e;
    --orange-dark: #b84e0a;
    --sun: #f4ea1a;
    --ink: #1a1a12;
    --ornament-red: #b3261e;
    --script-red: #9c1a10;
    --parchment: #f1dca6;
    --parchment-edge: #d9b878;
    --date-ink: #6b1608;
    --frame: #e6cf9c;
  }
  * { margin: 0; padding: 0; box-sizing: border-box; }
  html, body { width: 927px; height: 1200px; overflow: hidden; background: var(--green-deep); }
  .poster {
    position: relative; width: 927px; height: 1200px; overflow: hidden;
    background:
      repeating-linear-gradient(0deg, rgba(255,255,255,0.04) 0 3px, transparent 3px 48px),
      radial-gradient(ellipse at 40% 45%, var(--green-light) 0%, var(--green-mid) 45%, var(--green-deep) 100%);
    font-family: "Tillana", cursive;
  }
  .title {
    position: absolute; left: 22px; top: -18px; z-index: 3;
    font-size: 178px; font-weight: 800; color: var(--orange); letter-spacing: 4px;
    text-shadow: 2px 3px 0 var(--orange-dark), 0 0 12px rgba(0,0,0,0.35);
  }
  .sun-mark {
    position: absolute; left: 705px; top: 15px; width: 185px; height: 185px; z-index: 2;
    border-radius: 50%;
    background: radial-gradient(circle, var(--sun) 0%, var(--sun) 45%, rgba(244,234,26,0.6) 62%, rgba(244,234,26,0) 72%);
  }
  .subtitle-row {
    position: absolute; left: 30px; top: 196px; z-index: 5;
    display: flex; align-items: baseline; gap: 14px;
  }
  .shanti { font-family: "Tiro Devanagari Hindi", serif; font-size: 40px; color: var(--ink); }
  .subtitle {
    font-size: 90px; font-weight: 800; color: var(--orange); letter-spacing: 13px;
    text-shadow: 2px 3px 0 var(--orange-dark), 0 0 10px rgba(0,0,0,0.3);
  }
  .ornament {
    position: absolute; left: 80px; top: 300px; width: 560px; height: 560px; z-index: 1;
    background: radial-gradient(ellipse, rgba(179,38,30,0.75) 0%, rgba(179,38,30,0.45) 55%, rgba(179,38,30,0) 75%);
  }
  .tagline {
    position: absolute; left: 120px; width: 540px; text-align: center; z-index: 5;
    font-family: "Kaushan Script", cursive; color: var(--ink); font-size: 46px; letter-spacing: 2px;
    text-shadow: 0 0 6px rgba(255,255,255,0.55);
  }
  .tagline-1 { top: 318px; }
  .tagline-2 { top: 372px; }
  .tagline-mantra {
    position: absolute; left: 100px; width: 540px; top: 438px; text-align: center; z-index: 5;
    font-size: 54px; font-weight: 800; color: var(--ink); letter-spacing: 3px;
    text-shadow: 0 0 8px rgba(255,255,255,0.6);
  }
  .photo {
    position: absolute; border: 10px solid var(--frame); z-index: 4;
    box-shadow: 3px 5px 10px rgba(0,0,0,0.45);
  }
  .photo-singer { left: 585px; top: 225px; width: 370px; height: 225px; transform: rotate(-9deg);
    background: linear-gradient(135deg, #d9d4cc, #8a6a52 60%, #3a2a22); }
  .photo-harmonium { left: 565px; top: 420px; width: 350px; height: 290px; transform: rotate(4deg);
    background: linear-gradient(160deg, #c79a5a, #7d5a3a 55%, #3b2b20); }
  .photo-guitar { left: 585px; top: 690px; width: 360px; height: 245px; transform: rotate(-6deg);
    background: linear-gradient(150deg, #e6e0d2, #b58a4a 50%, #4a6a8a); }
  .invite {
    position: absolute; left: 0; width: 927px; text-align: center; z-index: 6;
    font-family: "Kaushan Script", cursive; color: var(--script-red); font-size: 48px; letter-spacing: 3px;
    text-shadow: 0 0 6px rgba(255,220,150,0.9), 0 0 2px rgba(255,220,150,0.9);
  }
  .invite-1 { top: 806px; }
  .invite-2 { top: 864px; font-size: 44px; letter-spacing: 2px; }
  .details {
    position: absolute; left: 15px; top: 950px; width: 900px; height: 240px; z-index: 6;
    background: radial-gradient(ellipse, var(--parchment) 55%, var(--parchment-edge) 100%);
    border: 2px solid #c9a560;
    display: flex; flex-direction: column; justify-content: center; align-items: center;
    color: var(--date-ink); font-weight: 700; font-size: 40px; line-height: 56px; letter-spacing: 3px;
  }
</style>
</head>
<body>
<main class="poster">
  <div class="ornament" role="img" aria-label="Red folk-art pattern of peacocks and flowers"></div>
  <h1 class="title">kirtan</h1>
  <div class="sun-mark" role="img" aria-label="Yellow sun emblem with sacred syllable"></div>
  <div class="photo photo-singer" role="img" aria-label="Photo of a woman singing with eyes closed"></div>
  <div class="photo photo-harmonium" role="img" aria-label="Photo of a woman playing harmonium"></div>
  <div class="photo photo-guitar" role="img" aria-label="Photo of a man singing with guitar at a microphone"></div>
  <div class="subtitle-row">
    <span class="shanti" lang="hi">शान्ति</span>
    <span class="subtitle">experience</span>
  </div>
  <p class="tagline tagline-1">An evening of music</p>
  <p class="tagline tagline-2">&amp; singing of sacred</p>
  <p class="tagline-mantra">mantra's</p>
  <p class="invite invite-1">Free Kirtan Experience</p>
  <p class="invite invite-2">with Mohan Priya Sevi &amp; Companions</p>
  <section class="details">
    <span>every friday night</span>
    <span>7:00pm-8:30pm</span>
    <span>kealoha pilates &amp; movement studio</span>
    <span>947 hollister rd, paia</span>
  </section>
</main>
</body>
</html>
```